VELMOR Website Design

We need a website designed for our company VELMOR. We are a luxury lifestyle club that will provide benefits and services for our members. The site should be clean & sleek, preferably using black and white (or darker colors). (example sites: stravenhall.example, plinth.example)

Here is a link of a sample page I did using wix. (https://dunmere7.sitehostly.example/mysite) This can be used to get a general idea.

Target Market(s)

Upper Middle Class in the United States

Number of Pages Required

5+ page

Font styles to use
Sans Serif
Other font styles liked:
• Arial (or other similar fonts)

Requirements
Must have
• A clean design that is eye-catching and speaks to our company.
Nice to have
• Ideas for copy.

```html
<!DOCTYPE html>
<html lang="en">
<head>
<meta charset="utf-8">
<title>VELMOR — Luxury Lifestyle Club</title>
<link href="https://fonts.googleapis.com/css2?family=Montserrat:wght@400;600;700&family=Open+Sans:wght@400;600&display=swap" rel="stylesheet">
<style>
:root{
  --ink:#1d1d1f;
  --muted:#555;
  --white:#ffffff;
  --dark:#1a1a1a;
  --footer:#222222;
  --line:#cfcfcf;
  --hero-a:#4a4d52;
  --hero-b:#1e1f22;
}
*{box-sizing:border-box;margin:0;padding:0}
html,body{width:1200px;height:2620px;overflow:hidden}
body{position:relative;font-family:"Open Sans",Arial,sans-serif;color:var(--ink);background:var(--white)}
.heading{font-family:"Montserrat",Arial,sans-serif}
.abs{position:absolute}

/* hero */
.hero{left:0;top:0;width:1200px;height:608px;background:linear-gradient(180deg,#6f7278 0%,var(--hero-a) 45%,var(--hero-b) 100%)}
.logo{left:128px;top:22px;font-family:"Montserrat",Arial,sans-serif;font-weight:600;font-size:38px;letter-spacing:3px;color:var(--white)}
.nav{right:128px;top:26px;display:flex;align-items:center;gap:30px;font-size:15px;color:var(--white)}
.nav .signin{border:1px solid var(--white);padding:8px 18px}
.hero-title{left:128px;top:246px;font-size:60px;line-height:72px;font-weight:700;color:var(--white)}
.btn{display:inline-block;background:var(--white);color:var(--ink);font-size:15px;padding:10px 18px;border:1px solid var(--line)}
.hero .btn{position:absolute;left:128px;top:384px}
.arrow{top:292px}

/* welcome */
.welcome-title{left:128px;top:686px;font-size:50px;font-weight:600}
.welcome-text{left:128px;top:762px;width:440px;font-size:16px;line-height:26px;color:var(--muted)}
.welcome-text p+p{margin-top:22px}
.welcome .btn{position:absolute;left:128px;top:932px}
.welcome-photo{left:648px;top:688px;width:416px;height:292px;background:linear-gradient(135deg,#8a7a6e,#3b332e);box-shadow:0 0 0 8px var(--white),0 4px 18px rgba(0,0,0,.25)}

/* benefits */
.benefits{left:0;top:1060px;width:1200px;height:612px;background:linear-gradient(180deg,#2a2a2c,#151516)}
.section-title{width:1200px;text-align:center;font-size:48px;font-weight:600}
.benefits .section-title{top:66px;color:var(--white)}
.benefits .lead{top:140px;width:1200px;text-align:center;font-size:17px;color:#e6e6e6}
.group-label{top:224px;font-size:17px;color:#e6e6e6}
.tile{width:124px;height:124px;background:var(--white);text-align:center;font-size:14px;line-height:17px;font-weight:600;color:var(--ink);padding-top:18px}
.tile svg{display:block;margin:0 auto 10px}
.tile.more{color:#999;font-weight:400}

/* experiences */
.exp .section-title{top:1730px}
.exp-text{top:1810px;width:1200px;text-align:center;font-size:16px;line-height:27px;color:var(--muted)}
.ph{display:block}
.view-all{left:548px;top:2390px}

/* footer */
.footer{left:0;top:2520px;width:1200px;height:100px;background:var(--footer);color:#bbb;font-size:13px}
.footer-links{left:128px;top:24px;display:flex;gap:22px}
.copyright{left:128px;top:58px;color:#888}
.social{right:128px;top:28px;display:flex;gap:20px}
.social span{width:22px;height:22px;border-radius:50%;background:#8a8a8a;display:block}
</style>
</head>
<body>

<section class="hero abs" role="img" aria-label="Photo of members in suits walking beside a private jet on the tarmac">
  <div class="logo abs">VELMOR</div>
  <nav class="nav abs">
    <span>Home</span><span>About Velmor</span><span>Benefits and Services</span><span>Experiences</span><span>Contact Us</span><span class="signin">Sign In</span>
  </nav>
  <h1 class="hero-title heading abs">Luxury Lifestyle<br>Club</h1>
  <a class="btn">Register Now</a>
  <svg class="arrow abs" style="left:40px" width="30" height="40" viewBox="0 0 30 40"><path d="M22 4 6 20l16 16" fill="none" stroke="#fff" stroke-width="5"/></svg>
  <svg class="arrow abs" style="right:40px" width="30" height="40" viewBox="0 0 30 40"><path d="M8 4l16 16L8 36" fill="none" stroke="#fff" stroke-width="5"/></svg>
</section>

<section class="welcome">
  <h2 class="welcome-title heading abs">Welcome to Velmor</h2>
  <div class="welcome-text abs">
    <p>VELMOR is a members only lifestyle club founded in order to bring the best services, experiences, and opportunities to our diverse community of members.</p>
    <p>Our members consist of creatives, athletes, artists, and other professionals.</p>
  </div>
  <a class="btn">Read More</a>
  <div class="welcome-photo abs" role="img" aria-label="Photo of members celebrating inside a limousine"></div>
</section>

<section class="benefits abs" role="img" aria-label="Dark photo backdrop of a members party">
  <h2 class="section-title heading abs">Benefits and Services</h2>
  <p class="lead abs">VELMOR membership provides you with amazing benefits and services.</p>

  <p class="group-label abs" style="left:128px">Members receive access to the best...</p>
  <div class="tile abs" style="left:128px;top:262px"><svg width="46" height="46" viewBox="0 0 46 46" fill="none" stroke="#222" stroke-width="2.5"><rect x="9" y="4" width="28" height="38" rx="2"/><rect x="14" y="9" width="18" height="8"/><path d="M15 24h4M21 24h4M27 24h4M15 30h4M21 30h4M27 30h4M15 36h4M21 36h4M27 36h4"/></svg>Accountants</div>
  <div class="tile abs" style="left:270px;top:262px"><svg width="46" height="46" viewBox="0 0 46 46" fill="none" stroke="#222" stroke-width="2.5"><path d="M23 5v34M12 40h22M8 12h30M8 12l-5 12h10zM38 12l-5 12h10z"/></svg>Attorneys</div>
  <div class="tile abs" style="left:412px;top:262px"><svg width="46" height="46" viewBox="0 0 46 46" fill="none" stroke="#222" stroke-width="2.5"><path d="M5 22 23 7l18 15M10 18v22h26V18"/><rect x="19" y="28" width="8" height="12"/></svg>Real estate<br>agents</div>
  <div class="tile abs" style="left:128px;top:404px"><svg width="46" height="46" viewBox="0 0 46 46" fill="none" stroke="#222" stroke-width="2.5"><path d="M5 16 23 6l18 10zM9 20v16M18 20v16M28 20v16M37 20v16M5 40h36"/></svg>Private<br>Bankers</div>
  <div class="tile abs" style="left:270px;top:404px"><svg width="46" height="46" viewBox="0 0 46 46" fill="none" stroke="#222" stroke-width="2.5"><circle cx="16" cy="14" r="6"/><circle cx="31" cy="14" r="6"/><path d="M5 38c0-8 5-13 11-13s11 5 11 13M22 30c2-3 5-5 9-5 6 0 10 5 10 13"/></svg>Private<br>Advisors</div>
  <div class="tile more abs" style="left:412px;top:404px"><svg width="46" height="46" viewBox="0 0 46 46" fill="none" stroke="#aaa" stroke-width="2.5"><circle cx="23" cy="23" r="17"/><path d="M23 14v18M14 23h18"/></svg>and more...</div>

  <p class="group-label abs" style="left:660px">Members receive access to private...</p>
  <div class="tile abs" style="left:660px;top:262px"><svg width="46" height="46" viewBox="0 0 46 46" fill="none" stroke="#222" stroke-width="2.5"><path d="M4 26h38M30 26 20 10h-5l5 16M16 26l-6 10h5l10-10M8 26l-4-8h4l4 8"/></svg>Private<br>flight travel</div>
  <div class="tile abs" style="left:802px;top:262px"><svg width="46" height="46" viewBox="0 0 46 46" fill="none" stroke="#222" stroke-width="2.5"><path d="M13 23h20M6 15v16M12 11v24M34 11v24M40 15v16"/></svg>Luxury gym<br>membership</div>
  <div class="tile abs" style="left:944px;top:262px"><svg width="46" height="46" viewBox="0 0 46 46" fill="none" stroke="#222" stroke-width="2.5"><circle cx="12" cy="14" r="5"/><circle cx="23" cy="11" r="5"/><circle cx="34" cy="14" r="5"/><path d="M4 34c0-7 4-11 8-11M42 34c0-7-4-11-8-11M14 38c0-9 4-14 9-14s9 5 9 14"/></svg>Private social<br>clubs</div>
  <div class="tile abs" style="left:660px;top:404px"><svg width="46" height="46" viewBox="0 0 46 46" fill="none" stroke="#222" stroke-width="2.5"><path d="M6 40h34M10 34V24M19 34V18M28 34V22M37 34V10"/></svg>Private<br>investment</div>
  <div class="tile abs" style="left:802px;top:404px"><svg width="46" height="46" viewBox="0 0 46 46" fill="none" stroke="#222" stroke-width="2.5"><path d="M4 30h38l-6 8H10zM10 30v-8h20l6 8M15 22v-6h10v6"/></svg>Private yacht</div>
  <div class="tile more abs" style="left:944px;top:404px"><svg width="46" height="46" viewBox="0 0 46 46" fill="none" stroke="#aaa" stroke-width="2.5"><circle cx="23" cy="23" r="17"/><path d="M23 14v18M14 23h18"/></svg>and more...</div>
</section>

<section class="exp">
  <h2 class="section-title heading abs">Experiences</h2>
  <p class="exp-text abs">VELMOR organizes and supports a ton of private events and parties for our members.<br>Members are also provided access to exclusive venues and events from our partners.<br>Network with other members to build lasting relationships.</p>
  <div class="ph abs" role="img" aria-label="Photo of travellers boarding a private jet" style="left:132px;top:1912px;width:216px;height:214px;background:linear-gradient(160deg,#b9c3cc,#5b6670)"></div>
  <div class="ph abs" role="img" aria-label="Photo of a speedboat on blue water" style="left:132px;top:2140px;width:216px;height:220px;background:linear-gradient(160deg,#2f8fb5,#1b4a68)"></div>
  <div class="ph abs" role="img" aria-label="Photo of passengers relaxing in a private jet cabin" style="left:362px;top:1912px;width:476px;height:448px;background:linear-gradient(160deg,#d8d2c8,#7a6f63)"></div>
  <div class="ph abs" role="img" aria-label="Photo of a woman on a yacht deck by the sea" style="left:852px;top:1912px;width:216px;height:214px;background:linear-gradient(160deg,#9fc3dc,#6e8fa3)"></div>
  <div class="ph abs" role="img" aria-label="Photo of a couple at an evening event" style="left:852px;top:2140px;width:216px;height:220px;background:linear-gradient(160deg,#c9c4bf,#3a3a3c)"></div>
  <a class="btn view-all abs">View All</a>
</section>

<footer class="footer abs">
  <div class="footer-links abs"><span>Home</span><span>About Velmor</span><span>Benefits and Services</span><span>Experiences</span><span>Contact Us</span><span>Sign In</span><span>Register</span></div>
  <div class="copyright abs">Copyright © 2019 · VELMOR · All rights reserved.</div>
  <div class="social abs"><span></span><span></span><span></span><span></span><span></span></div>
</footer>

</body>
</html>
```